A clean crisp business card for a Landscape Construction company. Designed to be easy to read contact/ info and also be appealing/interesting, unlike a traditional business card.

Industry/Entity Type

Landscape Construction

Contact Information for Business Card

Company name : Brambleford Landscape Construction, phone number: (877) 62Vista, website:Bramblefordyards.example, Email, sales@bramblefordyards.example

Requirements
Nice to have
• Luxurious finishes/ details…. Icons or emblems next to contact info
Should not have
• Clipart or general pictures

```html
<!DOCTYPE html>
<html lang="en">
<head>
<meta charset="utf-8">
<title>Brambleford Landscape Construction – Business Card</title>
<link rel="stylesheet" href="https://fonts.googleapis.com/css2?family=Cinzel:wght@600&family=Open+Sans:wght@400;600&display=swap">
<style>
  :root {
    --page-bg: #c9cbcc;
    --leaf-green: #9fcd3c;
    --leaf-green-deep: #8cbd2e;
    --brand-blue: #2168b8;
    --card-black: #141414;
    --card-black-soft: #1e1e1e;
    --text-white: #ffffff;
    --text-light: #e9e9e9;
  }
  * { box-sizing: border-box; margin: 0; padding: 0; }
  html, body { width: 1200px; height: 928px; overflow: hidden; }
  body {
    background: var(--page-bg);
    font-family: "Open Sans", Arial, sans-serif;
    position: relative;
  }
  .card {
    position: absolute;
    left: 265px;
    width: 672px;
    height: 384px;
    border-radius: 16px;
    overflow: hidden;
  }
  .card--front {
    top: 58px;
    background: linear-gradient(90deg, var(--leaf-green-deep), var(--leaf-green) 60%, #a9d54a);
    display: flex;
    align-items: center;
    justify-content: center;
  }
  .front-name {
    color: var(--text-white);
    font-weight: 600;
    font-size: 24px;
    letter-spacing: 1px;
    display: flex;
    align-items: center;
    gap: 10px;
    margin-top: -22px;
  }
  .front-name .dot {
    width: 14px; height: 14px; border-radius: 50%;
    background: var(--text-white);
  }
  .card--back {
    top: 486px;
    background: radial-gradient(ellipse at 60% 30%, var(--card-black-soft), var(--card-black) 70%);
  }
  .wave { position: absolute; left: 0; top: 0; width: 672px; height: 384px; }
  .person { position: absolute; left: 41px; top: 42px; }
  .person__name {
    font-family: "Cinzel", Georgia, serif;
    font-weight: 600;
    font-size: 29px;
    letter-spacing: 1.5px;
    line-height: 1;
  }
  .person__name .first { color: var(--brand-blue); }
  .person__name .last { color: var(--leaf-green); }
  .person__title { color: var(--text-light); font-size: 15px; margin-top: 9px; }
  .brand {
    position: absolute;
    right: 34px;
    top: 128px;
    width: 250px;
    text-align: center;
    color: var(--leaf-green);
    font-weight: 600;
    font-size: 17px;
    line-height: 1.35;
    letter-spacing: 1.5px;
  }
  .contacts { position: absolute; left: 41px; top: 196px; list-style: none; }
  .contacts li {
    display: flex; align-items: center; gap: 8px;
    color: var(--text-light);
    font-size: 15px;
    height: 33px;
  }
  .contacts svg { width: 16px; height: 16px; fill: var(--leaf-green); flex: none; }
  .address {
    position: absolute;
    right: 32px;
    top: 308px;
    text-align: right;
    color: var(--text-white);
    font-weight: 600;
    font-size: 15.5px;
    line-height: 27px;
  }
</style>
</head>
<body>
  <section class="card card--front" role="img" aria-label="Green card front with a faint repeating emblem pattern">
    <div class="front-name"><span class="dot"></span>Brambleford</div>
  </section>

  <section class="card card--back">
    <svg class="wave" viewBox="0 0 672 384" aria-hidden="true">
      <path d="M0 268 C70 330 140 360 230 352 C360 340 470 260 672 276 L672 384 L0 384 Z" fill="#2168b8"/>
      <path d="M0 262 C70 326 140 354 230 346 C360 334 470 254 672 270" fill="none" stroke="#9fcd3c" stroke-width="6"/>
      <path d="M0 266 C70 330 140 358 230 350 C360 338 470 258 672 274" fill="none" stroke="#111" stroke-width="2"/>
    </svg>

    <div class="person">
      <h1 class="person__name"><span class="first">Daniel</span> <span class="last">Harrow</span></h1>
      <p class="person__title">Director</p>
    </div>

    <div class="brand">Brambleford<br>Landscape Construction</div>

    <ul class="contacts">
      <li>
        <svg viewBox="0 0 24 24"><path d="M6.6 10.8a15.1 15.1 0 0 0 6.6 6.6l2.2-2.2a1 1 0 0 1 1-.25 11.4 11.4 0 0 0 3.6.57 1 1 0 0 1 1 1V20a1 1 0 0 1-1 1A17 17 0 0 1 3 4a1 1 0 0 1 1-1h3.5a1 1 0 0 1 1 1c0 1.25.2 2.45.57 3.57a1 1 0 0 1-.25 1z"/></svg>
        <span>(877) 62Vista</span>
      </li>
      <li>
        <svg viewBox="0 0 24 24"><path d="M2 5h20v2l-10 6L2 7z"/><path d="M2 9l10 6 10-6v10H2z"/></svg>
        <span>sales@bramblefordyards.example</span>
      </li>
      <li>
        <svg viewBox="0 0 24 24"><circle cx="12" cy="12" r="10"/><path d="M8 7c2 0 3 2 2 3s-3 1-3 3 2 2 2 4" fill="none" stroke="#141414" stroke-width="1.6"/><path d="M15 5c-1 2 1 3 2 4s0 3 2 4" fill="none" stroke="#141414" stroke-width="1.6"/></svg>
        <span>www.bramblefordyards.example</span>
      </li>
    </ul>

    <address class="address" style="font-style:normal">
      4127 Larkspur Valley Rd<br>
      NUM 318, Fairhaven, OH 45990
    </address>
  </section>
</body>
</html>
```